Business Card Design Project

Business Card
We are rebranding with a new logo
Industry/Entity Type
Business
Contact Information for Business Card
Dennis Morvale +61 487215963 dennis@quorv.com.au P.O. Box 872 Fernlow QLD 4309
Requirements
Must have
- Logo

```html
<!DOCTYPE html>
<html lang="en">
<head>
<meta charset="utf-8">
<title>Quorv International – Business Card</title>
<link href="https://fonts.googleapis.com/css2?family=Arimo:wght@400;700&display=swap" rel="stylesheet">
<style>
  :root {
    --backdrop: #24272c;
    --card: #ffffff;
    --brand-blue: #1a8cc2;
    --art-orange: #f39a22;
    --art-blue: #0b78a6;
    --text-dark: #333638;
    --text-muted: #7a7d80;
  }
  html, body {
    margin: 0;
    padding: 0;
    width: 1200px;
    height: 902px;
    overflow: hidden;
    background: var(--backdrop);
    font-family: "Arimo", Arial, sans-serif;
  }
  .business-card {
    position: absolute;
    left: 170px;
    top: 188px;
    width: 860px;
    height: 525px;
    border-radius: 26px;
    background: var(--card);
    overflow: hidden;
  }
  .card-artwork {
    position: absolute;
    top: 0;
    right: 0;
    width: 290px;
    height: 100%;
    background: linear-gradient(90deg, var(--art-orange) 0%, var(--art-orange) 45%, var(--art-blue) 100%);
  }
  .brand-name {
    position: absolute;
    left: 56px;
    top: 70px;
    margin: 0;
    font-size: 34px;
    font-weight: 700;
    color: var(--brand-blue);
  }
  .person {
    position: absolute;
    left: 120px;
    top: 200px;
  }
  .person-name {
    margin: 0;
    font-size: 32px;
    font-weight: 700;
    color: var(--brand-blue);
  }
  .person-role {
    margin: 4px 0 0 26px;
    font-size: 17px;
    color: var(--text-muted);
  }
  .contact-list {
    position: absolute;
    left: 150px;
    top: 300px;
    margin: 0;
    padding: 0;
    list-style: none;
    font-size: 22px;
    color: var(--text-dark);
    line-height: 1.25;
  }
  .contact-item {
    display: flex;
    align-items: flex-start;
    gap: 18px;
  }
  .contact-item + .contact-item { margin-top: 6px; }
  .contact-item.address { margin-bottom: 26px; }
  .contact-icon {
    width: 22px;
    height: 22px;
    flex: none;
    margin-top: 3px;
    fill: var(--brand-blue);
  }
</style>
</head>
<body>
  <article class="business-card">
    <div class="card-artwork" role="img" aria-label="Decorative orange and blue sweeping artwork"></div>

    <h1 class="brand-name">Quorv International</h1>

    <div class="person">
      <h2 class="person-name">Dennis Morvale</h2>
      <p class="person-role">Owner</p>
    </div>

    <ul class="contact-list">
      <li class="contact-item address">
        <svg class="contact-icon" viewBox="0 0 24 24" aria-hidden="true"><path d="M12 3 2 12h3v9h5v-6h4v6h5v-9h3z"/></svg>
        <span>P.O. Box 872<br>Fernlow QLD 4309</span>
      </li>
      <li class="contact-item phone">
        <svg class="contact-icon" viewBox="0 0 24 24" aria-hidden="true"><path d="M7 1h10a2 2 0 0 1 2 2v18a2 2 0 0 1-2 2H7a2 2 0 0 1-2-2V3a2 2 0 0 1 2-2zm0 3v14h10V4zm5 15.5a1.2 1.2 0 1 0 0 2.4 1.2 1.2 0 0 0 0-2.4z"/></svg>
        <span>+61 487215963</span>
      </li>
      <li class="contact-item email">
        <svg class="contact-icon" viewBox="0 0 24 24" aria-hidden="true"><path d="M2 5h20v14H2zm2 2v.5l8 5.5 8-5.5V7zm0 3v7h16v-7l-8 5.5z"/></svg>
        <span>dennis@quorv.com.au</span>
      </li>
    </ul>
  </article>
</body>
</html>
```